Dalvick's Business Card

I need some designs for a new business card including the new logo attached. An old example of our business card is also attached to show all the data that should be included on the new design.
**I added some more examples someone had mocked up**

Contact Information for Business Card

Should include all info on other examples uploaded.

```html
<!DOCTYPE html>
<html lang="en">
<head>
<meta charset="utf-8">
<title>Dalvick's Business Card</title>
<link rel="stylesheet" href="https://fonts.googleapis.com/css2?family=Montserrat:wght@600;700&family=Poppins:wght@400;500;600;700&display=swap">
<style>
  :root {
    --page: #262626;
    --card: #0a0a0a;
    --blue: #1a7fd4;
    --red: #e0262b;
    --white: #f2f2f2;
    --grey: #b8b8b8;
  }
  * { box-sizing: border-box; margin: 0; padding: 0; }
  html, body { width: 1200px; height: 900px; overflow: hidden; }
  body {
    background: var(--page);
    font-family: "Poppins", sans-serif;
    display: flex;
    flex-direction: column;
    align-items: center;
    justify-content: center;
    gap: 40px;
  }
  .card {
    width: 700px;
    height: 400px;
    background: var(--card);
    border-radius: 26px;
    position: relative;
    box-shadow: 0 14px 30px rgba(0,0,0,.45);
  }
  .brand {
    position: absolute;
    display: flex;
    align-items: center;
    gap: 16px;
  }
  .brand-dot {
    width: 58px; height: 58px;
    border-radius: 50%;
  }
  .brand-text { display: flex; flex-direction: column; }
  .brand-name {
    font-family: "Montserrat", sans-serif;
    font-weight: 700;
    font-size: 58px;
    line-height: 1;
    letter-spacing: 1px;
  }
  .brand-tagline {
    font-family: "Montserrat", sans-serif;
    font-weight: 600;
    font-size: 13px;
    letter-spacing: 1px;
    margin-top: 4px;
    text-align: right;
  }

  /* front */
  .card-front .brand { left: 150px; top: 80px; }
  .card-front .brand-dot { background: var(--blue); }
  .card-front .brand-name { color: var(--blue); }
  .card-front .brand-tagline { color: var(--red); }
  .owner-name {
    position: absolute;
    left: 0; right: 0; top: 195px;
    text-align: center;
    font-family: "Montserrat", sans-serif;
    font-weight: 700;
    font-size: 30px;
    color: var(--blue);
    letter-spacing: 1px;
  }
  .front-footer {
    position: absolute;
    left: 60px; right: 40px; top: 270px;
    display: flex;
    align-items: center;
    gap: 22px;
  }
  .credentials {
    color: var(--red);
    font-weight: 600;
    font-size: 20px;
    line-height: 1.35;
    text-align: right;
  }
  .divider { width: 1px; height: 64px; background: var(--white); }
  .contact-list { list-style: none; color: var(--blue); font-size: 19px; line-height: 1.5; }
  .contact-list li { display: flex; align-items: center; gap: 10px; }
  .contact-list svg { width: 20px; height: 20px; flex: none; }

  /* back */
  .card-back .brand { left: 170px; top: 70px; }
  .card-back .brand-dot { background: var(--white); }
  .card-back .brand-name { color: var(--grey); }
  .card-back .brand-tagline { color: var(--grey); }
  .service-area {
    position: absolute;
    left: 0; right: 0; top: 190px;
    text-align: center;
    color: var(--white);
    font-weight: 700;
    font-size: 24px;
  }
  .rule {
    position: absolute;
    left: 290px; width: 120px; top: 238px;
    height: 1px; background: var(--grey);
  }
  .call-to-action {
    position: absolute;
    left: 90px; right: 90px; top: 256px;
    text-align: center;
    color: var(--white);
    font-weight: 500;
    font-size: 18px;
    line-height: 1.4;
    text-transform: uppercase;
  }
</style>
</head>
<body>
  <section class="card card-front">
    <div class="brand">
      <span class="brand-dot"></span>
      <div class="brand-text">
        <span class="brand-name">DALVICK'S</span>
        <span class="brand-tagline">AIR CONDITIONING &amp; HEATING SERVICE</span>
      </div>
    </div>
    <h1 class="owner-name">MARK DALVICK</h1>
    <div class="front-footer">
      <p class="credentials">Licensed &amp; Insured<br>Family Owned &amp; Operated</p>
      <span class="divider"></span>
      <ul class="contact-list">
        <li>
          <svg viewBox="0 0 24 24" aria-hidden="true"><path fill="#e0262b" d="M6.6 10.8a15.2 15.2 0 0 0 6.6 6.6l2.2-2.2a1 1 0 0 1 1-.25 11.4 11.4 0 0 0 3.6.57 1 1 0 0 1 1 1V20a1 1 0 0 1-1 1A17 17 0 0 1 3 4a1 1 0 0 1 1-1h3.5a1 1 0 0 1 1 1c0 1.25.2 2.45.57 3.57a1 1 0 0 1-.25 1z"/></svg>
          555.014.2290
        </li>
        <li>
          <svg viewBox="0 0 24 24" aria-hidden="true"><rect x="2" y="5" width="20" height="14" rx="1" fill="#e0262b"/><path d="M2.5 5.5 12 13l9.5-7.5" fill="none" stroke="#0a0a0a" stroke-width="1.6"/></svg>
          dalvickhvac@mail.com
        </li>
      </ul>
    </div>
  </section>

  <section class="card card-back">
    <div class="brand">
      <span class="brand-dot"></span>
      <div class="brand-text">
        <span class="brand-name">DALVICK'S</span>
        <span class="brand-tagline">AIR CONDITIONING &amp; HEATING SERVICE</span>
      </div>
    </div>
    <p class="service-area">Serves Maple Falls, IA &amp; Surrounding Areas</p>
    <span class="rule"></span>
    <p class="call-to-action">Call today for all your HVAC, refrigeration &amp;<br>plumbing needs</p>
  </section>
</body>
</html>
```